Digital Marketing Website Redesign, modern, fresh, dynamic

Hi there, we would like to freshen up our website and create a new dynamic look. We are a digital marketing agency who specialise in digital transformation in the form of creating websites for appointment bookings. Our clients are service businesses such as hairdressers, dentists and doctors who's patients need to book appointments with them.

Our company name is Tallomex with the point being we can help increase your revenue curve by increasing your appointment bookings.

Our services include building the website, creating campaigns to drive traffic, increasing conversions and monitoring and reporting.

We are playing with a tagline of 'Step into your Digital Transformation' as we have a 5 step journey that customers can take with us getting them from zero to full appointment bookings.

Our current website is www.tallomex-sample.com

You can see a draft design that I mocked up on Canva here https://www.draftboard-sample.com/design/QXB82LmpR7T/KpoW39dnFsYbZet_wqe_OPa/edit?utm_content=QXB82LmpR7T&utm_campaign=designshare&utm_medium=link2&utm_source=sharebutton

Also attached some other homepage ideas. In regard to photos we are open to ideas.

Please let if you need any more information to provide us with an initial design. Thanks million and I look forward to receiving fantastic designs :)

Marian Dobbs
Tallomex

Target Market(s)

Appointment based businesses such as hairdressers, dentists, doctors

Industry/Entity Type

Marketing and Digital

Coding

Coded - Design and coding required

Number of Pages Required

1 page

Colors
0094D4
00A9DD
6FCCEA
C7EBF8
E9F6FB

Requirements
Must have
• Appointment booking CTA
Nice to have
• A website we like https://www.fergalwhitty-sample.ie

```html
<!DOCTYPE html>
<html lang="en">
<head>
<meta charset="utf-8">
<title>Tallomex – Step Into Your Digital Transformation</title>
<link rel="stylesheet" href="https://fonts.googleapis.com/css2?family=Roboto:wght@400;500;700&display=swap">
<style>
:root{
  --navy:#1f3f78;
  --navy-dark:#0c1a33;
  --bar:#4b6a99;
  --lime:#c8d400;
  --lime-soft:#dfe68a;
  --text:#2b2b2b;
  --muted:#666;
  --cream:#f6f6ee;
  --white:#fff;
}
*{box-sizing:border-box;margin:0;padding:0}
html,body{width:1200px;height:3564px;overflow:hidden}
body{font-family:'Roboto',sans-serif;color:var(--text);background:var(--white);position:relative}
.abs{position:absolute}
.btn{position:absolute;display:flex;align-items:center;justify-content:center;background:var(--lime);color:var(--navy);font-weight:500;font-size:15px;border-radius:24px}
.center{left:0;width:1200px;text-align:center}

/* top bar */
.topbar{top:0;left:0;width:1200px;height:52px;background:var(--bar);border-bottom:1px solid #9db0cc}
.social{top:16px;width:18px;height:18px;border-radius:3px;background:#dfe6f1}
.contact{top:15px;color:#fff;font-size:16px;display:flex;align-items:center;gap:12px}

/* hero */
.hero{top:52px;left:0;width:1200px;height:608px;background:radial-gradient(ellipse at 50% 55%,#4d6f96 0%,#1c2d4a 40%,#0a1222 80%)}
.logo{top:110px;left:110px;color:#fff;font-size:40px;font-weight:700;letter-spacing:.5px}
.nav{top:153px;right:110px;display:flex;gap:38px;color:#fff;font-size:15px}
.tag{top:278px;left:510px;width:180px;height:40px;background:#3f6bb8;color:#fff;font-weight:700;font-size:18px;display:flex;align-items:center;justify-content:center;border-radius:3px}
.hero-title{top:336px;color:#fff;font-size:52px;font-weight:700;line-height:64px}
.hero-text{top:411px;left:220px;width:760px;text-align:center;color:#fff;font-size:18px;font-weight:500;line-height:35px}

/* why */
.orbit{top:783px;left:165px;width:336px;height:336px;border:2px dashed #d8e3a0;border-radius:50%}
.hub{top:870px;left:237px;width:190px;height:190px;border-radius:50%;background:#fff;box-shadow:0 0 0 12px #f1f2ea,0 6px 18px rgba(0,0,0,.08);display:flex;align-items:center;justify-content:center;color:var(--navy);font-size:30px;font-weight:700}
.avatar{border-radius:50%;border:3px solid #fff;box-shadow:0 3px 10px rgba(0,0,0,.15);background:linear-gradient(135deg,#c9a58a,#e9dccf)}
.why h2{top:768px;left:643px;font-size:33px;color:var(--navy);font-weight:700}
.why h3{top:838px;left:643px;font-size:17px;color:var(--navy);font-weight:700}
.why .quote{top:872px;left:643px;width:430px;font-size:14px;color:var(--muted);line-height:28px}
.stars{top:941px;left:643px;color:#f2a20d;font-size:16px;letter-spacing:1px}
.person{top:973px;left:643px;font-size:17px;color:var(--text);font-weight:500}
.role{top:1005px;left:643px;font-size:13px;color:var(--navy)}
.dots{top:1042px;left:643px;display:flex;gap:5px}
.dots i{width:8px;height:8px;border-radius:50%;background:var(--lime-soft)}
.dots i:first-child{background:#8fa800}

.stat{top:1248px;text-align:center}
.stat b{display:block;font-size:44px;color:#2f5ba8;font-weight:700;margin-top:4px}
.stat span{font-size:18px;color:var(--text)}
.divider{top:1252px;width:1px;height:115px;background:#e5e5d5}

/* steps */
.steps{top:1465px;left:0;width:1200px;height:618px;background:radial-gradient(ellipse at 28% 55%,#3e7fb8 0%,#13284a 35%,#091428 70%)}
.steps-title{top:1533px;left:599px;color:#fff;font-size:32px;font-weight:700}
.acc{left:600px;width:488px;background:#fff;border-radius:8px;padding:0 32px}
.acc h4{font-size:18px;color:var(--navy);font-weight:700;line-height:56px;display:flex;justify-content:space-between;align-items:center}
.acc p{font-size:12.5px;color:#555;line-height:24px;margin-top:-8px}
.bars{top:1935px;left:600px;display:flex;gap:6px}
.bars i{height:4px;background:#fff;border-radius:2px}

/* team */
.team h2{top:2150px;font-size:35px;color:var(--navy);font-weight:700}
.team .lead{top:2213px;left:170px;width:860px;text-align:center;font-size:15px;color:var(--muted);line-height:31px}
.card{top:2320px;width:228px;height:293px;background:#fff;box-shadow:0 2px 12px rgba(0,0,0,.08);text-align:center}
.card .photo{margin:5px;height:184px}
.card .name{margin-top:28px;font-size:16px;color:var(--text)}
.card .job{margin-top:9px;font-size:16px;color:var(--text);font-weight:500}

/* pricing */
.pricing{top:2768px;left:0;width:1200px;height:744px;background:var(--cream)}
.pricing-title{top:2822px;font-size:35px;color:var(--navy);font-weight:700}
.pricing-lead{top:2883px;font-size:15px;color:var(--muted)}
.plan{top:2938px;width:313px;height:345px;background:#fff;border-radius:10px;box-shadow:0 2px 10px rgba(0,0,0,.06)}
.plan .head{margin:5px;height:89px;background:var(--navy);border-radius:8px;color:#fff;text-align:center;padding-top:14px}
.plan .head h4{font-size:18px;font-weight:500}
.plan .head .price{font-size:28px;font-weight:500;margin-top:4px}
.plan .head .price small{font-size:10px;margin-left:8px}
.feat{position:absolute;left:26px;right:20px;font-size:13px;color:var(--muted);line-height:31px;padding-left:22px}
.feat b{color:var(--navy);font-weight:500}
.feat svg{position:absolute;left:0;top:10px}
.note{top:3390px;left:170px;width:860px;text-align:center;font-size:15px;color:var(--muted);line-height:31px}

/* footer */
.footer{top:3512px;left:0;width:1200px;height:52px;background:var(--navy);color:#fff;font-size:13px}
.footer span{position:absolute;top:19px}
</style>
</head>
<body>

<!-- top bar -->
<div class="abs topbar"></div>
<div class="abs social" style="left:111px"></div>
<div class="abs social" style="left:140px"></div>
<div class="abs social" style="left:169px"></div>
<div class="abs social" style="left:198px"></div>
<div class="abs contact" style="left:705px">
  <svg width="18" height="13" viewBox="0 0 18 13"><rect width="18" height="13" rx="1.5" fill="#fff"/><path d="M1 1l8 6 8-6" stroke="#4b6a99" stroke-width="1.6" fill="none"/></svg>info@tallomex-sample.com</div>
<div class="abs contact" style="left:930px">
  <svg width="17" height="17" viewBox="0 0 17 17"><rect width="17" height="17" rx="3" fill="#fff"/><path d="M5 4c0 5 3 8 8 8l0-2-2.3-1-1 1c-1.5-.7-2.5-1.7-3.2-3.2l1-1L6.5 4z" fill="#4b6a99"/></svg>+1 555 010 0199</div>

<!-- hero -->
<header>
<div class="abs hero" role="img" aria-label="Person walking through a glowing digital tunnel"></div>
<div class="abs logo">Tallomex</div>
<div class="btn" style="top:87px;left:883px;width:205px;height:41px">Book An Appointment</div>
<nav class="abs nav"><span>Digital Transformation Consultancy</span><span>5 Steps</span><span>Our Pricing</span><span>Ahead Of The Curve</span><span>Our Team</span></nav>
<div class="abs tag">#appointments</div>
<h1 class="abs center hero-title">Step Into Your Digital Transformation</h1>
<p class="abs hero-text">Digital transformation is a journey. At Tallomex we divide the journey into five key steps that take your business from comprehensive market research to full appointment bookings. Ready to go on that journey?</p>
<div class="btn" style="top:540px;left:536px;width:128px;height:41px">Start Here</div>
</header>

<!-- why -->
<section class="why">
<div class="abs orbit"></div>
<div class="abs hub">Tallomex</div>
<div class="abs avatar" style="top:834px;left:150px;width:72px;height:72px" role="img" aria-label="Client portrait"></div>
<div class="abs avatar" style="top:780px;left:390px;width:72px;height:72px" role="img" aria-label="Client portrait"></div>
<div class="abs avatar" style="top:940px;left:436px;width:106px;height:106px;border:4px solid var(--lime)" role="img" aria-label="Client portrait"></div>
<div class="abs avatar" style="top:1055px;left:210px;width:72px;height:72px" role="img" aria-label="Client portrait"></div>
<h2 class="abs">Why others choose us?</h2>
<h3 class="abs">100 Bookings In First Month!</h3>
<p class="abs quote">Tallomex's booking system helped us get over 100 appointment bookings in May 2020.</p>
<div class="abs stars">★★★★★</div>
<div class="abs person">Lena Farrow</div>
<div class="abs role">Owner, Shear Studio</div>
<div class="abs dots"><i></i><i></i><i></i><i></i></div>
<div class="btn" style="top:1080px;left:643px;width:129px;height:43px">View More</div>

<div class="abs stat" style="left:100px;width:196px">
  <svg width="40" height="40" viewBox="0 0 40 40" fill="none" stroke="#c8d400" stroke-width="2"><rect x="3" y="6" width="30" height="28" rx="2"/><path d="M3 13h30M10 3v6M26 3v6"/><circle cx="31" cy="31" r="6" fill="#fff"/><path d="M28 31l2 2 4-4"/></svg>
  <b>762</b><span>Appointments Booked</span></div>
<div class="abs divider" style="left:328px"></div>
<div class="abs stat" style="left:360px;width:200px">
  <svg width="40" height="40" viewBox="0 0 40 40" fill="none" stroke="#c8d400" stroke-width="2"><rect x="3" y="3" width="14" height="14"/><rect x="23" y="3" width="14" height="14"/><rect x="3" y="23" width="14" height="14"/><path d="M23 30h14M30 23v14"/></svg>
  <b>31</b><span>Marketing Campaigns</span></div>
<div class="abs divider" style="left:590px"></div>
<div class="abs stat" style="left:630px;width:235px">
  <svg width="40" height="40" viewBox="0 0 40 40" fill="none" stroke="#c8d400" stroke-width="2"><path d="M6 34l10-10 6 6 12-14"/><path d="M27 16h7v7"/><circle cx="20" cy="10" r="6"/></svg>
  <b>25%</b><span>Website Traffic Increase</span></div>
<div class="abs divider" style="left:903px"></div>
<div class="abs stat" style="left:940px;width:187px">
  <svg width="40" height="40" viewBox="0 0 40 40" fill="none" stroke="#c8d400" stroke-width="2"><circle cx="20" cy="16" r="10"/><path d="M15 30h10M16 35h8M20 6v-3M8 16H5M35 16h-3"/></svg>
  <b>∞</b><span>Creative Ideas</span></div>
</section>

<!-- steps -->
<section>
<div class="abs steps" role="img" aria-label="Open hand holding glowing blue digital butterflies"></div>
<h2 class="abs steps-title">5 steps</h2>
<div class="abs acc" style="top:1609px;height:141px">
  <h4>Creative Campaigns <svg width="16" height="16" viewBox="0 0 16 16"><circle cx="8" cy="8" r="8" fill="#1f3f78"/><path d="M8 12V5M5 8l3-3 3 3" stroke="#fff" stroke-width="1.8" fill="none"/></svg></h4>
  <p>I must explain to you how all this mistaken idea of denouncing pleasure and praising pain was born and I will give you a complete account of the system, and expound the actual teachings of the great</p>
</div>
<div class="abs acc" style="top:1772px;height:56px"><h4>Market Research <svg width="16" height="16" viewBox="0 0 16 16"><circle cx="8" cy="8" r="8" fill="#1f3f78"/><path d="M8 4v7M5 8l3 3 3-3" stroke="#fff" stroke-width="1.8" fill="none"/></svg></h4></div>
<div class="abs acc" style="top:1849px;height:56px"><h4>Online Bookings <svg width="16" height="16" viewBox="0 0 16 16"><circle cx="8" cy="8" r="8" fill="#1f3f78"/><path d="M8 4v7M5 8l3 3 3-3" stroke="#fff" stroke-width="1.8" fill="none"/></svg></h4></div>
<div class="abs bars"><i style="width:72px"></i><i style="width:14px"></i><i style="width:14px"></i></div>
<div class="btn" style="top:1965px;left:600px;width:128px;height:43px">Sign up</div>
</section>

<!-- team -->
<section class="team">
<h2 class="abs center">Our Team</h2>
<p class="abs lead">From business management and web development to creative campaign delivery and social media expertise, our team has all the experience your business needs to it to the top of its digital game.</p>
<div class="abs card" style="left:110px"><div class="photo" style="background:linear-gradient(135deg,#4b4339,#b59a7e)" role="img" aria-label="Account manager in an office meeting"></div><div class="name">Declan</div><div class="job">Account Manager</div></div>
<div class="abs card" style="left:360px"><div class="photo" style="background:linear-gradient(135deg,#cfd3d6,#8f9bb0)" role="img" aria-label="Account manager holding a tablet"></div><div class="name">Ronan</div><div class="job">Account Manager</div></div>
<div class="abs card" style="left:611px"><div class="photo" style="background:linear-gradient(135deg,#2d5f92,#c99a8e)" role="img" aria-label="Website specialist at a desk"></div><div class="name">Maya</div><div class="job">Website specialist</div></div>
<div class="abs card" style="left:863px"><div class="photo" style="background:linear-gradient(135deg,#f2f2f2,#a9c6de)" role="img" aria-label="Social media specialist portrait"></div><div class="name">Sofia</div><div class="job">Social media specialist</div></div>
<div class="btn" style="top:2648px;left:536px;width:128px;height:42px">View More</div>
</section>

<!-- pricing -->
<section>
<div class="abs pricing"></div>
<h2 class="abs center pricing-title">Our Pricing</h2>
<p class="abs center pricing-lead">Which plan you take will depend on how many steps you want to take on your digital transformation journey.</p>

<div class="abs plan" style="left:106px">
  <div class="head"><h4>Starter Plan</h4><div class="price">€399<small>/a month</small></div></div>
  <div class="feat" style="top:128px"><svg width="13" height="12" viewBox="0 0 13 12" fill="none" stroke="#1f3f78" stroke-width="1.6"><rect x="1" y="1" width="10" height="10"/><path d="M3 6l2.5 2.5L12 1.5"/></svg><b>Step 1:</b> Online readiness review based on our 12 point checklist</div>
  <div class="feat" style="top:221px"><svg width="13" height="12" viewBox="0 0 13 12" fill="none" stroke="#1f3f78" stroke-width="1.6"><rect x="1" y="1" width="10" height="10"/><path d="M3 6l2.5 2.5L12 1.5"/></svg><b>Step 2:</b> Implementation</div>
  <div class="btn" style="top:275px;left:28px;width:257px;height:42px">Take 2 Steps</div>
</div>
<div class="abs plan" style="left:443px">
  <div class="head"><h4>Premium Plan</h4><div class="price">€599<small>/a month</small></div></div>
  <div class="feat" style="top:128px"><svg width="13" height="12" viewBox="0 0 13 12" fill="none" stroke="#1f3f78" stroke-width="1.6"><rect x="1" y="1" width="10" height="10"/><path d="M3 6l2.5 2.5L12 1.5"/></svg><b>Steps</b>&nbsp; 1, 2 &amp; 3</div>
  <div class="feat" style="top:190px"><svg width="13" height="12" viewBox="0 0 13 12" fill="none" stroke="#1f3f78" stroke-width="1.6"><rect x="1" y="1" width="10" height="10"/><path d="M3 6l2.5 2.5L12 1.5"/></svg><b>Step 2:</b> Content is King</div>
  <div class="btn" style="top:275px;left:28px;width:257px;height:42px">Take 3 Steps</div>
</div>
<div class="abs plan" style="left:781px">
  <div class="head"><h4>Starter Plan</h4><div class="price">€399<small>/a month</small></div></div>
  <div class="feat" style="top:128px"><svg width="13" height="12" viewBox="0 0 13 12" fill="none" stroke="#1f3f78" stroke-width="1.6"><rect x="1" y="1" width="10" height="10"/><path d="M3 6l2.5 2.5L12 1.5"/></svg><b>Steps</b> 1, 2, 3, 4 &amp; 5</div>
  <div class="feat" style="top:190px"><svg width="13" height="12" viewBox="0 0 13 12" fill="none" stroke="#1f3f78" stroke-width="1.6"><rect x="1" y="1" width="10" height="10"/><path d="M3 6l2.5 2.5L12 1.5"/></svg><b>Step 4 :</b>&nbsp; Marketing Campaign</div>
  <div class="feat" style="top:221px"><svg width="13" height="12" viewBox="0 0 13 12" fill="none" stroke="#1f3f78" stroke-width="1.6"><rect x="1" y="1" width="10" height="10"/><path d="M3 6l2.5 2.5L12 1.5"/></svg><b>Step 5 :</b>&nbsp; Monitor and Maintain</div>
  <div class="btn" style="top:275px;left:28px;width:257px;height:42px">Take The Full Journey</div>
</div>

<div class="btn" style="top:3327px;left:463px;width:274px;height:42px">More Info About The Five Steps</div>
<p class="abs note">All plans include: Dedicated account manager - Minimum 3 months subscription Marketing campaign can be implemented after one month - Additional activities charged at €65 per hour</p>
</section>

<!-- footer -->
<footer class="abs footer">
  <span style="left:110px">(C) Copyright 2024 | All Rights Reserved</span>
  <span style="left:800px">Privacy Policy</span>
  <span style="left:924px">|</span>
  <span style="left:972px">Terms Of Conditions</span>
  <span style="left:1159px">C58</span>
</footer>

</body>
</html>
```